Property Developer - Simple yet Sophisticated and Sharp Business Card

We are a medium sized property developer involved mainly in townhouse developments and land subdivisions.

The company is looking for a simple, sharp and sophisticated business card that will be given to contractors, land owners, financiers etc and thus will need to look professional.

Property development related graphics and art can be used, however the card is not to be too "busy" or crowded. Our company name is Kestrel Developments which could possibly be incorporated into the graphics or artwork.

Single sided and/or double sided designs will be acceptable.

A Simple, Sophisticated, Sharp design please!

Good Luck !

```html
<!DOCTYPE html>
<html lang="en">
<head>
<meta charset="utf-8">
<title>Kestrel Developments – Business Card</title>
<link rel="stylesheet" href="https://fonts.googleapis.com/css2?family=Montserrat:wght@400;700&display=swap">
<style>
  :root {
    --page: #ffffff;
    --card: #453014;
    --ink: #ffffff;
    --ink-soft: #ddd3c4;
    --rule: #f4efe8;
  }
  * { margin: 0; padding: 0; box-sizing: border-box; }
  html, body {
    width: 1200px; height: 900px; overflow: hidden;
    background: var(--page);
    font-family: "Montserrat", Arial, sans-serif;
  }
  .card {
    position: absolute; left: 68px; top: 126px;
    width: 1064px; height: 648px;
    background: var(--card);
    color: var(--ink);
  }
  .double-rule {
    position: absolute; left: 58px; width: 948px;
  }
  .double-rule span {
    display: block; position: absolute; left: 0; right: 0;
    background: var(--rule);
  }
  .double-rule .thick { top: 0; height: 3px; }
  .double-rule .thin { top: 7px; height: 2px; }
  .rule-top { top: 68px; }
  .rule-bottom { top: 466px; }

  .company-name {
    position: absolute; left: 58px; top: 80px;
    font-weight: 700; font-size: 33px; letter-spacing: 0.2px;
    text-transform: uppercase; line-height: 1.2;
  }
  .person-name {
    position: absolute; left: 58px; top: 404px;
    font-weight: 700; font-size: 33px; line-height: 1.2;
    text-transform: uppercase;
  }
  .person-role {
    position: absolute; left: 59px; top: 442px;
    font-weight: 400; font-size: 15px; line-height: 1.2;
    color: var(--ink-soft); text-transform: uppercase; letter-spacing: 0.4px;
  }
  .contact {
    position: absolute; top: 486px;
    text-transform: uppercase;
  }
  .contact-phone { left: 58px; }
  .contact-email { left: 294px; }
  .contact-postal { left: 740px; }
  .contact .label {
    display: block; font-weight: 400; font-size: 14px; line-height: 18px;
    color: var(--ink-soft); letter-spacing: 0.4px;
  }
  .contact .value {
    display: block; font-weight: 700; font-size: 24px; line-height: 30px;
    margin-top: 1px;
  }
  .contact .label + .value + .label { margin-top: 6px; }
</style>
</head>
<body>
  <div class="card">
    <div class="double-rule rule-top"><span class="thick"></span><span class="thin"></span></div>
    <h1 class="company-name">Kestrel Developments</h1>

    <h2 class="person-name">James Whitford</h2>
    <p class="person-role">Project Manager</p>

    <div class="double-rule rule-bottom"><span class="thick"></span><span class="thin"></span></div>

    <div class="contact contact-phone">
      <span class="label">Phone</span>
      <span class="value">(07) 3555 0192</span>
      <span class="label">Fax</span>
      <span class="value">(07) 3555 0193</span>
    </div>
    <div class="contact contact-email">
      <span class="label">Email</span>
      <span class="value">projects.kestreldev<br>@mailhub.com</span>
    </div>
    <div class="contact contact-postal">
      <span class="label">Postal</span>
      <span class="value">PO Box 2875<br>Maplewood North<br>QLD 4172</span>
    </div>
  </div>
</body>
</html>
```